Professional looking Roller Blind Discount Card that portrays quality at a value for money price!

We need a double sided business card designed as a discount card. Size 90mm wide x 55mm high.We would like it to look professional and portray quality at a value for money price point.I have uploaded a word document with a basic layout with the information we want included on each side of the card. Please put your own thought into the layout.

Contact Information for Business Card

As per word document attached.

```html
<!DOCTYPE html>
<html lang="en">
<head>
<meta charset="utf-8">
<title>Roller Blinds Discount Card</title>
<link href="https://fonts.googleapis.com/css2?family=Montserrat:wght@400;500;600;700&display=swap" rel="stylesheet">
<style>
  :root {
    --backdrop: #c9cccf;
    --card: #151717;
    --blue: #29a3dc;
    --white: #ffffff;
    --gold-light: #f8dc72;
    --gold: #d9a623;
    --gold-dark: #9c6d0c;
  }
  * { box-sizing: border-box; margin: 0; padding: 0; }
  html, body {
    width: 1200px; height: 800px; overflow: hidden;
    background: var(--backdrop);
    font-family: "Montserrat", sans-serif;
  }
  .canvas {
    position: relative; width: 1200px; height: 800px;
    display: flex; justify-content: center; align-items: center; gap: 30px;
  }
  .card {
    position: relative; width: 560px; height: 342px;
    background: var(--card); color: var(--white);
    box-shadow: 0 6px 18px rgba(0,0,0,.25);
    overflow: hidden;
  }
  /* front side */
  .offer {
    position: absolute; top: 14px; left: 0; width: 100%;
    display: flex; justify-content: center; align-items: flex-start;
    color: var(--blue); font-weight: 600;
  }
  .offer-number { font-size: 104px; line-height: 1; letter-spacing: -2px; }
  .offer-suffix { display: flex; flex-direction: column; margin-left: 4px; margin-top: 14px; line-height: .9; }
  .offer-percent { font-size: 48px; }
  .offer-off { font-size: 36px; }
  .product-line {
    position: absolute; top: 128px; width: 100%; text-align: center;
    font-size: 21px; font-weight: 500;
  }
  .range-line {
    position: absolute; top: 158px; width: 100%; text-align: center;
    font-size: 19px;
  }
  .range-line .divider { color: var(--blue); padding: 0 4px; }
  .seals {
    position: absolute; top: 196px; left: 0; width: 100%;
    display: flex; justify-content: space-around; padding: 0 40px;
  }
  .seal { width: 92px; height: 92px; }
  .call {
    position: absolute; font-size: 22px; font-weight: 500; white-space: nowrap;
  }
  .call .phone { color: var(--blue); }
  .front .call { top: 298px; width: 100%; text-align: center; }
  /* back side */
  .back-title {
    position: absolute; top: 18px; left: 0; width: 100%; text-align: center;
    color: var(--blue); font-size: 46px; font-weight: 700; letter-spacing: 1px;
  }
  .back-subtitle {
    position: absolute; top: 76px; left: 0; width: 100%; text-align: center;
    font-size: 19px; font-weight: 500;
  }
  .back-subtitle .free { color: var(--blue); }
  .window-photo {
    position: absolute; top: 112px; left: 28px; width: 272px; height: 162px;
    border: 2px solid var(--blue);
    background: linear-gradient(160deg, #c9c2b6 0%, #8f9f7a 35%, #4f6b39 65%, #7a5a3c 100%);
  }
  .back .call { top: 290px; left: 28px; }
  .burst {
    position: absolute; top: 108px; left: 322px; width: 220px; height: 170px;
  }
  .burst svg { position: absolute; inset: 0; }
  .burst-text {
    position: absolute; inset: 0; display: flex; align-items: center; justify-content: center;
    text-align: center; font-size: 22px; font-weight: 500; line-height: 1.15; color: var(--white);
  }
  .brand {
    position: absolute; top: 298px; left: 322px; width: 220px; text-align: center;
    color: var(--white); font-size: 16px; font-weight: 500;
  }
</style>
</head>
<body>
<main class="canvas">
  <section class="card front" aria-label="Card front">
    <div class="offer">
      <span class="offer-number">25</span>
      <span class="offer-suffix"><span class="offer-percent">%</span><span class="offer-off">OFF</span></span>
    </div>
    <p class="product-line">Quality Custom Made ROLLER BLINDS</p>
    <p class="range-line">Blockout<span class="divider">|</span>Screen<span class="divider">|</span>Light Filtering</p>
    <div class="seals">
      <svg class="seal" viewBox="0 0 92 92" aria-hidden="true">
        <defs>
          <radialGradient id="goldFill" cx="40%" cy="35%" r="70%">
            <stop offset="0" stop-color="#f8dc72"/>
            <stop offset=".6" stop-color="#d9a623"/>
            <stop offset="1" stop-color="#9c6d0c"/>
          </radialGradient>
        </defs>
        <circle cx="46" cy="46" r="45" fill="url(#goldFill)"/>
        <circle cx="46" cy="46" r="34" fill="none" stroke="#9c6d0c" stroke-width="2"/>
      </svg>
      <svg class="seal" viewBox="0 0 92 92" aria-hidden="true">
        <circle cx="46" cy="46" r="45" fill="url(#goldFill)"/>
        <circle cx="46" cy="46" r="34" fill="none" stroke="#9c6d0c" stroke-width="2"/>
      </svg>
      <svg class="seal" viewBox="0 0 92 92" aria-hidden="true">
        <circle cx="46" cy="46" r="45" fill="url(#goldFill)"/>
        <circle cx="46" cy="46" r="34" fill="none" stroke="#9c6d0c" stroke-width="2"/>
      </svg>
    </div>
    <p class="call">Call <span class="phone">0400 123 456</span> Today</p>
  </section>

  <section class="card back" aria-label="Card back">
    <h1 class="back-title">ROLLER BLINDS</h1>
    <p class="back-subtitle"><span class="free">FREE</span> in Home Measure &amp; Quote</p>
    <div class="window-photo" role="img" aria-label="Photo of a room with roller blinds above large windows looking onto garden greenery"></div>
    <p class="call">Call <span class="phone">0400 123 456</span> Today</p>
    <div class="burst">
      <svg viewBox="0 0 220 170" aria-hidden="true">
        <polygon fill="#29a3dc" points="218,85 185.3,100 203.5,126 165.1,126 164,156 130.2,141 110,167 89.8,141 56,156 54.9,126 16.5,126 34.7,100 2,85 34.7,70 16.5,44 54.9,44 56,14 89.8,29 110,3 130.2,29 164,14 165.1,44 203.5,44 185.3,70"/>
      </svg>
      <p class="burst-text">Huge<br>Selection<br>Of Fabrics</p>
    </div>
    <p class="brand">Northway Interiors</p>
  </section>
</main>
</body>
</html>
```